A unique communication angle to crowdfunding

Looking for a fresh redesign of a crowd funding website that deals in real estate. I already have the content, but am looking to take the design to the next level.

Existing real estate crowd funding sites focus on the real estate. I want to explore communication angle that:
- puts the investor in the centre of the communication: "become a duke"
- highlights the international nature (international properties, international investors)

There's also quite a lot of copy on the site, as we need to explain the service in quite a bit of detail. There's room to reduce the copy and replace with graphics. Could also consider clicking to see different text (see our difference section in http://galleonfairs.com)

The backend of the platform is already being worked on by a specialist crowd funding service provider.

In total there are 5 pages to be designed.

The homepage is really important. Right now it looks quite dated. It doesn't have a great layout. Note there is no mobile version of the website, so the pages need to be seen well on mobile devices. When looking at the brief, refer to the following links too:

current website:
http://pennyduke.com

some revisions made so far:
http://preview.stakeharbor.com/7K3LQ9

Attached are logo files and another file which contained copy for the pages. No need to rework the logo.

Please make sure to use the same copy in the brief on the webpages, to ensure the layouts work. Designers are free to propose images they feel work on the pages.

I would like to see if rather than tweaking the pages, it's possible to come up with a better design concept. If the 5 pages are accepted, there's a chance I'll request an additional 4 pages.
Updates

Please note the font used in the logo is called "harabara" in case you decide to use it in any of the titles, etc.

Please note there is one additional page for which we would like to review designs. Note the page would be a template to be used on all future real estate detail pages. Here is an example of the current design for reference:

http://pennyduke.com/projects/view/14

In total there are 5 page designs required, (homepage + 4)

Thank you

FYI -

Just a quick note to give information from similar UK real estate crowdfunding sites:
http://www.housewalrus.co.uk
http://tiderock.co.uk
https://www.fundquarry.com

Of the above, only tiderock has a nice clean looking landing page. Information is clear and well laid out.

Hi all, just uploaded a new file in the brief. Contains some comments and a website reference. I thought it may help to explain how we could convey international aspect as well as how we could convey images in a more modern way. This is an option you can consider, but its entirely up to you how how answer the brief. Thanks!

Reason: As requested by some designers needing more time to complete their work. Continue to share your work in progress and receive timely feedback before the deadline.

We would like to let you know that we have just shortlisted the best designs. Together with that, we have also passed some detailed feedback to all designers who weren't shortlisted. If we didn't contact you, please let us know. If you haven't submitted a design or are working on revisions, please note these will no longer be taken into account now. We hope you understand that we need to close the project today. Thank you all once again for your great work and design concepts. Here's hoping we meet again on a future design brief. Cheers, pennyduke team.

Target Market(s)

At the moment, only rich are able to buy real estate. With this service, anyone can become a landlord. Target buyers:

Young professionals, looking to diversify from stock market and lower risk
People nearing retirement, looking for stable rental incomes
Retirees - looking to supplement pensions with possibility of capital gains
Parents - looking for a way to save long term for their children (instead of low interest paying bank accounts)

Industry/Entity Type

Communication

Font styles to use
Sans Serif
Other font styles liked:
• harabara

Colors
add136
f5f9eb
959595
000000

Requirements
Must have
• Overall, the site must convey "whoever you are, you too can become a landlord", and that you don't need to be wealthy to invest in real estate. See

Communication should put the investor (or the duke) at the centre. The investor can be any of those described in the target market.

Show the aspirational side of property ownership.

In addition to the investor/duke character, the second main theme is international. No other real estate crowdfunding website highlights this.
Nice to have
• Banner could show different consumer types, to illustrate that the service can appeal to many different profiles. Refer to attached file "home page reference - plainasbread.com" as an example of how this could be done.

Aim to show the international side of the service. Properties around the world, investors around the world.

```html
<!DOCTYPE html>
<html lang="en">
<head>
<meta charset="utf-8">
<title>pennyduke – Home</title>
<link href="https://fonts.googleapis.com/css2?family=Open+Sans:wght@400;600;700&display=swap" rel="stylesheet">
<style>
:root{
  --green:#add136;
  --green-text:#8db22a;
  --green-band:#a9cd33;
  --cream:#f5f9eb;
  --grey:#959595;
  --grey-light:#ebebeb;
  --dark:#262626;
  --dark-btn:#333333;
  --text:#555555;
  --black:#000000;
  --white:#ffffff;
}
*{box-sizing:border-box;margin:0;padding:0}
html,body{width:1200px;height:3066px;overflow:hidden}
body{font-family:'Open Sans',Arial,sans-serif;color:var(--text);background:var(--white);position:relative}
.section{position:absolute;left:0;width:1200px}
.center{text-align:center}

/* header */
.site-header{top:0;height:147px;border-bottom:2px solid #d9d9d9;background:var(--white)}
.brand{position:absolute;left:100px;top:62px;display:flex;align-items:center;gap:12px}
.brand-dot{width:34px;height:34px;border-radius:50%;background:var(--green)}
.brand-name{font-size:36px;font-weight:700;color:var(--green-text);letter-spacing:-0.5px}
.social{position:absolute;top:32px;left:754px;display:flex;gap:8px}
.social span{width:24px;height:24px;border-radius:50%;background:var(--green)}
.search{position:absolute;left:905px;top:30px;width:193px;height:32px;border:1px solid #d4d4d4;font-size:13px;color:#999;padding:7px 10px}
.search svg{position:absolute;right:6px;top:6px}
.main-nav{position:absolute;right:100px;top:116px;display:flex;gap:34px;font-size:14px;color:#444}
.main-nav a{color:inherit;text-decoration:none;position:relative}
.main-nav a.active{color:var(--green-text)}
.main-nav a.active::after{content:"";position:absolute;left:-4px;right:-4px;top:28px;height:4px;background:var(--green)}

/* hero */
.hero{top:147px;height:507px;background:var(--cream);overflow:hidden}
.hero h1{position:absolute;top:44px;left:150px;width:900px;text-align:center;font-size:31px;font-weight:400;color:#777;line-height:1.35}
.hero-art{position:absolute;left:0;right:0;top:150px;bottom:0;background:linear-gradient(180deg,#f5f9eb 0%,#dfe8ef 45%,#c9d5dc 80%,#b5c28a 100%)}
.hero-arrow{position:absolute;top:236px;width:34px;height:34px;border-radius:50%;background:#cfcfcf}
.hero-arrow svg{position:absolute;left:9px;top:9px}

/* intro */
.intro{top:654px;height:231px}
.intro h2{margin-top:42px;font-size:29px;font-weight:400;color:var(--green-text)}
.intro p{width:820px;margin:14px auto 0;font-size:14px;line-height:1.6;color:#777}
.intro p+p{margin-top:12px}

/* split */
.split{top:885px;height:305px;display:flex}
.split-col{position:relative;width:600px;height:305px;color:var(--white)}
.split-col.members{background:var(--green-band)}
.split-col.buyers{background:var(--dark)}
.split-col h3{position:absolute;top:100px;font-size:37px;font-weight:700}
.split-col .lead{position:absolute;top:152px;font-size:19px;font-weight:700;line-height:1.25}
.split-col .small{position:absolute;top:182px;font-size:15px;font-weight:600}
.members h3,.members .lead,.members .small{left:110px}
.buyers h3,.buyers .lead{left:33px}
.buyers .lead{font-size:16px;font-weight:600;line-height:1.6;top:154px}
.btn{display:inline-block;font-family:inherit;font-size:18px;font-weight:600;padding:9px 18px;border-radius:3px;border:none}
.members .btn{position:absolute;left:115px;top:229px;background:var(--dark-btn);color:var(--white)}
.buyers .btn{position:absolute;left:38px;top:229px;background:var(--green);color:var(--black)}
.icon-building{position:absolute;left:470px;top:31px}
.icon-person{position:absolute;left:393px;top:24px;width:92px;height:96px;background:linear-gradient(180deg,#f2f2f2,#cfcfcf);border-radius:46px 46px 8px 8px}

/* projects */
.projects{top:1190px;height:686px}
.projects h2{margin-top:60px;font-size:29px;font-weight:400;color:var(--green-text)}
.projects .sub{width:640px;margin:14px auto 0;font-size:14px;line-height:1.6;color:#777}
.card{position:absolute;top:190px;width:314px;height:405px;border:1px solid #dcdcdc;background:var(--white)}
.card .price{height:56px;background:var(--green);color:var(--white);font-size:22px;font-weight:600;text-align:center;line-height:56px}
.card .photo{height:147px}
.card h4{margin-top:14px;text-align:center;font-size:17px;font-weight:600;color:var(--green-text)}
.card .desc{width:270px;margin:6px auto 0;text-align:center;font-size:12px;line-height:1.6;color:#888}
.progress{position:absolute;left:20px;right:20px;top:325px;height:10px;background:#e6e6e6}
.progress span{display:block;height:100%;background:var(--green)}
.funded{position:absolute;left:20px;top:344px;font-size:14px;color:#666}
.card .btn{position:absolute;left:85px;bottom:-26px;width:143px;background:var(--dark-btn);color:var(--white);font-size:17px;text-align:center;padding:8px 0}

/* newsletter */
.newsletter{top:1876px;height:180px;background:var(--grey-light)}
.newsletter h2{margin-top:26px;font-size:30px;font-weight:600;color:#333}
.newsletter p{font-size:12px;color:#666;margin-top:2px}
.signup{position:absolute;top:106px;left:415px;display:flex;gap:8px}
.signup .field{width:270px;height:40px;background:var(--white);border:1px solid #d4d4d4;font-size:12px;color:#999;padding:11px 14px;text-align:left}
.signup .submit{width:94px;height:40px;background:#555;color:var(--white);font-size:15px;font-weight:600;line-height:40px;text-align:center;border-radius:2px}

/* community */
.community{top:2056px;height:495px}
.community h2{margin-top:44px;font-size:30px;font-weight:400;color:var(--green-text)}
.community .sub{margin-top:8px;font-size:14px;color:#777}
.benefit{position:absolute;top:152px;width:260px;text-align:center;font-size:15px;color:#222;line-height:1.5}
.benefit svg{display:block;margin:0 auto 10px}
.press{position:absolute;left:120px;top:299px;width:960px;height:143px;border:1px solid #d9d9d9;background:var(--white)}
.press .label{position:absolute;left:14px;top:10px;font-size:11px;color:#444}
.press .mark{position:absolute;height:26px;background:#cfcfcf;border-radius:2px}

/* legal */
.legal{top:2551px;height:368px;background:var(--grey-light)}
.legal-box{position:absolute;left:120px;width:960px;background:var(--white);padding:18px 22px;font-size:11.5px;line-height:1.75;color:#999;overflow:hidden}

/* footer */
.site-footer{top:2919px;height:147px;background:#2b2b2b}
.footer-nav{position:absolute;top:38px;left:0;width:1200px;text-align:center;font-size:12px;color:#ccc}
.footer-nav span{margin:0 10px}
.copyright{position:absolute;left:100px;top:98px;font-size:12px;color:#bbb}
.footer-social{position:absolute;right:100px;top:94px;display:flex;gap:8px}
.footer-social span{width:24px;height:24px;border-radius:50%;background:#777}
</style>
</head>
<body>

<header class="section site-header">
  <div class="brand"><span class="brand-dot"></span><span class="brand-name">pennyduke</span></div>
  <div class="social"><span></span><span></span><span></span><span></span></div>
  <div class="search">Search
    <svg width="18" height="18" viewBox="0 0 18 18"><circle cx="7.5" cy="7.5" r="5.5" fill="none" stroke="#777" stroke-width="2"/><line x1="11.5" y1="11.5" x2="16" y2="16" stroke="#777" stroke-width="2"/></svg>
  </div>
  <nav class="main-nav">
    <a class="active">Home</a><a>Sign In</a><a>How it Works</a><a>Discover A Project</a><a>The Duke Blog</a><a>Find Out More</a>
  </nav>
</header>

<section class="section hero">
  <div class="hero-art" role="img" aria-label="Illustration of a young investor holding a magnifying glass over a property, beside a modern city skyline"></div>
  <h1>The pennyduke community is social and collaborative. Pool<br>with friends. Share any gains.</h1>
  <div class="hero-arrow" style="left:30px"><svg width="16" height="16" viewBox="0 0 16 16"><path d="M10 3 5 8l5 5" fill="none" stroke="#fff" stroke-width="2.5"/></svg></div>
  <div class="hero-arrow" style="right:30px"><svg width="16" height="16" viewBox="0 0 16 16"><path d="M6 3l5 5-5 5" fill="none" stroke="#fff" stroke-width="2.5"/></svg></div>
</section>

<section class="section intro center">
  <h2>pennyduke is reconstructing a property ladder that's strong and fair</h2>
  <p>By harnessing the power of crowds, it's possible to become a landlord in attractive locations around the world without the burden of financing 100% of the purchase. Leave the day to day management of your property portfolio to us.</p>
  <p>Start with as little as 1% in a project and plan your steps to becoming a true duke.</p>
</section>

<section class="section split">
  <div class="split-col members">
    <svg class="icon-building" width="94" height="86" viewBox="0 0 94 86">
      <rect x="4" y="4" width="86" height="78" fill="none" stroke="#262626" stroke-width="7"/>
      <g fill="#262626">
        <rect x="17" y="16" width="14" height="12"/><rect x="40" y="16" width="14" height="12"/><rect x="63" y="16" width="14" height="12"/>
        <rect x="17" y="37" width="14" height="12"/><rect x="40" y="37" width="14" height="12"/><rect x="63" y="37" width="14" height="12"/>
        <rect x="17" y="58" width="14" height="12"/><rect x="40" y="58" width="14" height="24"/><rect x="63" y="58" width="14" height="12"/>
      </g>
    </svg>
    <h3>Find Properties</h3>
    <div class="lead">Sign up to browse the portfolio.</div>
    <div class="small">Your journey to becoming a real estate duke starts here.</div>
    <span class="btn">Become a Member</span>
  </div>
  <div class="split-col buyers">
    <div class="icon-person" role="img" aria-label="Business person icon"></div>
    <h3>Find Buyers</h3>
    <div class="lead">Submit a property or development and raise funds<br>from our real estate dukes.</div>
    <span class="btn">Submit Your Project</span>
  </div>
</section>

<section class="section projects center">
  <h2>Featured Projects</h2>
  <p class="sub">Brief details of new and popular projects. To view full listings, you will be required to sign up and become a member.</p>

  <article class="card" style="left:100px">
    <div class="price">From GBP 3,600</div>
    <div class="photo" role="img" aria-label="Photo of a waterfront city skyline" style="background:linear-gradient(180deg,#bcd9ee 0%,#7ea9c9 55%,#3d86b3 100%)"></div>
    <h4>14 Harbour Row London E3</h4>
    <p class="desc">Class aptent taciti sociosqu ad litora torquent per conubia nostra, per inceptos himenaeos. Donec ac sem id lorem ultrices.</p>
    <div class="progress"><span style="width:0%"></span></div>
    <div class="funded">0% &nbsp;funded</div>
    <span class="btn">View more</span>
  </article>

  <article class="card" style="left:444px">
    <div class="price">From GBP 3,600</div>
    <div class="photo" role="img" aria-label="Photo of a brick and stone commercial building" style="background:linear-gradient(180deg,#dfe9f2 0%,#a6876c 45%,#6e5443 80%,#8a8a86 100%)"></div>
    <h4>14 Harbour Row London E3</h4>
    <p class="desc">Class aptent taciti sociosqu ad litora torquent per conubia nostra, per inceptos himenaeos. Donec ac sem id lorem ultrices.</p>
    <div class="progress"><span style="width:6%"></span></div>
    <div class="funded">4% &nbsp;funded</div>
    <span class="btn">View more</span>
  </article>

  <article class="card" style="left:787px">
    <div class="price">From GBP 3,600</div>
    <div class="photo" role="img" aria-label="Photo of a large apartment building with arched windows" style="background:linear-gradient(180deg,#7fb0dc 0%,#d7b898 45%,#b98d68 80%,#7f8b4e 100%)"></div>
    <h4>14 Harbour Row London E3</h4>
    <p class="desc">Class aptent taciti sociosqu ad litora torquent per conubia nostra, per inceptos himenaeos. Donec ac sem id lorem ultrices.</p>
    <div class="progress"><span style="width:51%"></span></div>
    <div class="funded">51% &nbsp;funded</div>
    <span class="btn">View more</span>
  </article>
</section>

<section class="section newsletter center">
  <h2>Get In Touch</h2>
  <p>sign up to receive additional information on new projects and get the newsletter</p>
  <div class="signup"><div class="field">E-mail Address</div><div class="submit">SUBMIT</div></div>
</section>

<section class="section community center">
  <h2>Be Part of a Growing International Community</h2>
  <p class="sub">Gain access to new projects in world class cities and join our growing community of international landlords.</p>
  <div class="benefit" style="left:138px">
    <svg width="36" height="36" viewBox="0 0 36 36"><circle cx="18" cy="18" r="18" fill="#8a8a8a"/><path d="M10 18.5l5.5 5.5L26.5 12.5" fill="none" stroke="#fff" stroke-width="3.5"/></svg>
    A community of international<br>property dukes.
  </div>
  <div class="benefit" style="left:469px">
    <svg width="36" height="36" viewBox="0 0 36 36"><circle cx="18" cy="18" r="18" fill="#8a8a8a"/><path d="M10 18.5l5.5 5.5L26.5 12.5" fill="none" stroke="#fff" stroke-width="3.5"/></svg>
    Collective buying power of<br>the pennyduke community
  </div>
  <div class="benefit" style="left:804px">
    <svg width="36" height="36" viewBox="0 0 36 36"><circle cx="18" cy="18" r="18" fill="#8a8a8a"/><path d="M10 18.5l5.5 5.5L26.5 12.5" fill="none" stroke="#fff" stroke-width="3.5"/></svg>
    Attractive real estate from<br>around the world
  </div>
  <div class="press">
    <span class="label">Featured in</span>
    <span class="mark" style="left:28px;top:38px;width:122px"></span>
    <span class="mark" style="left:182px;top:38px;width:130px"></span>
    <span class="mark" style="left:362px;top:34px;width:140px"></span>
    <span class="mark" style="left:542px;top:30px;width:84px;height:40px"></span>
    <span class="mark" style="left:656px;top:30px;width:46px;height:40px"></span>
    <span class="mark" style="left:724px;top:38px;width:136px"></span>
    <span class="mark" style="left:18px;top:88px;width:64px;height:30px"></span>
    <span class="mark" style="left:104px;top:86px;width:110px;height:32px"></span>
    <span class="mark" style="left:278px;top:90px;width:340px"></span>
  </div>
</section>

<section class="section legal">
  <div class="legal-box" style="top:35px;height:139px">By accessing this site and any pages thereof, you agree to be bound by the terms and conditions. This website is only suitable, intended and available for professional or sophisticated, or similar investors in other jurisdictions, or those who are members of pennyduke community and familiar with, and willing to, accept the risks associated with private participation. Pennyduke does not endorse any of the projects that appear on this website, nor does it make any recommendations regarding the appropriateness of particular opportunities for any participant. Each potential participant must review and evaluate the projects in his or her own discretion and determine the suitability of participating.</div>
  <div class="legal-box" style="top:190px;height:145px">This website (the "Site") is in every respect unaffiliated with any site to which it links or to any company or entity (and connected projects, investment opportunity or similar) featured on this Site, and is not meant as an endorsement of any of those companies or entities ("third parties"). Furthermore and for the avoidance of doubt, Pennyduke Limited is in no way affiliated with any third parties featured or referenced on this Site. There is no commercial relationship between Pennyduke Limited and such third parties, nor an agency arrangement or similar. If you believe your Content (including third party content) as each such term is defined in our Terms of Service has been reproduced on the Site with-</div>
</section>

<footer class="section site-footer">
  <div class="footer-nav"><span>• Terms of Service</span><span>• Privacy Policy</span><span>• How it Works</span><span>• Discover A Project</span><span>• The Duke Blog</span><span>• FAQ</span><span>• Contact</span></div>
  <div class="copyright">Copyright &nbsp;© &nbsp;2014 &nbsp;Pennyduke. &nbsp;&nbsp;All rights reserved.</div>
  <div class="footer-social"><span></span><span></span><span></span><span></span></div>
</footer>

</body>
</html>
```